Corvane Capital Business Cards

These are professional business cards that are for my family office.
Put fake emails and phone numbers as of now until I finalize those components. This family office controls my families investments, assets, and future. The cards should be professional.
..
.
.
.
I just uploaded another variation of a logo I would like to see as a business card to I am inbeteen which logo to use

Target Market(s)

business

Industry/Entity Type

business

Contact Information for Business Card

Professional, wealth related, finance related.

Requirements
Must have
• Logo

```html
<!DOCTYPE html>
<html lang="en">
<head>
<meta charset="utf-8">
<title>Corvane Capital Business Cards</title>
<link rel="stylesheet" href="https://fonts.googleapis.com/css2?family=Montserrat:wght@400;500;700&display=swap">
<style>
  :root {
    --backdrop: #6f5640;
    --card-white: #ffffff;
    --navy: #1b1f30;
    --navy-deep: #141826;
    --navy-lift: #2a3048;
    --silver: #9a9ca4;
    --ink: #1b1f30;
  }
  * { margin: 0; padding: 0; box-sizing: border-box; }
  html, body {
    width: 900px; height: 1200px; overflow: hidden;
    background: var(--backdrop);
    font-family: "Montserrat", Arial, sans-serif;
    color: var(--ink);
  }
  .canvas { position: relative; width: 900px; height: 1200px; }

  .card {
    position: absolute;
    border-radius: 22px;
    overflow: hidden;
    box-shadow: 0 8px 18px rgba(0,0,0,0.35);
  }
  .card-front { left: 80px; top: 130px; width: 742px; height: 442px; background: var(--card-white); }
  .card-back  { left: 78px; top: 637px; width: 744px; height: 443px; background: var(--navy); }

  .brand-name {
    position: absolute; left: 28px; top: 48px;
    font-size: 42px; font-weight: 700; letter-spacing: 1px;
    color: var(--ink); text-transform: uppercase;
  }
  .holder { position: absolute; right: 49px; top: 60px; text-align: right; }
  .holder-name { font-size: 26px; font-weight: 700; line-height: 1.2; }
  .holder-role { font-size: 16px; font-weight: 400; margin-top: 2px; }

  .address {
    position: absolute; left: 28px; top: 250px;
    font-size: 17px; line-height: 21px; font-weight: 400;
  }
  .contacts { position: absolute; left: 28px; top: 327px; list-style: none; }
  .contacts li {
    display: flex; align-items: center; gap: 9px;
    font-size: 17px; height: 28px;
  }
  .contacts svg { width: 16px; height: 16px; fill: var(--ink); flex: none; }

  .brand-seal {
    position: absolute; left: 472px; top: 175px;
    width: 240px; height: 240px;
    border: 4px solid var(--ink); border-radius: 50%;
    display: flex; align-items: center; justify-content: center;
    text-align: center;
    font-size: 22px; font-weight: 700; line-height: 1.25; text-transform: uppercase;
    color: var(--ink);
  }

  .back-pattern {
    position: absolute; inset: 0;
    background: linear-gradient(135deg, #5a6078 0%, var(--navy-lift) 30%, var(--navy) 55%, var(--navy-deep) 100%);
  }
  .back-seal {
    position: absolute; left: 586px; top: 270px;
    width: 72px; height: 72px;
    border: 2px solid var(--card-white); border-radius: 50%;
    display: flex; align-items: center; justify-content: center;
    text-align: center;
    color: var(--card-white);
    font-size: 9px; font-weight: 700; line-height: 1.2; text-transform: uppercase;
  }
</style>
</head>
<body>
<main class="canvas">

  <section class="card card-front" aria-label="Business card front">
    <div class="brand-name">Corvane Capital</div>

    <div class="holder">
      <div class="holder-name">Martin Oduya</div>
      <div class="holder-role">Owner</div>
    </div>

    <address class="address" style="font-style:normal">
      42 Linden Court Plaza<br>
      Ashbury, NJ 07815 USA
    </address>

    <ul class="contacts">
      <li>
        <svg viewBox="0 0 24 24" aria-hidden="true"><path d="M6.6 10.8a15.1 15.1 0 0 0 6.6 6.6l2.2-2.2a1 1 0 0 1 1-.25 11.4 11.4 0 0 0 3.6.57 1 1 0 0 1 1 1V20a1 1 0 0 1-1 1A17 17 0 0 1 3 4a1 1 0 0 1 1-1h3.5a1 1 0 0 1 1 1c0 1.25.2 2.45.57 3.6a1 1 0 0 1-.25 1z"/></svg>
        (555)014-2876
      </li>
      <li>
        <svg viewBox="0 0 24 24" aria-hidden="true"><path d="M2 5h20v14H2z M2 5l10 7 10-7" fill="none" stroke="#1b1f30" stroke-width="0"/><path d="M2 6v12h20V6l-10 7z"/><path d="M2 4h20l-10 7z"/></svg>
        info@yourwebsitename.com
      </li>
      <li>
        <svg viewBox="0 0 24 24" aria-hidden="true"><circle cx="12" cy="12" r="10"/><path d="M7 7c2 0 3 1 3 3s-2 2-2 4 1 3 1 5M14 4c0 2 2 3 4 3M15 13c1 0 3 1 3 3s-1 3-2 4" stroke="#fff" stroke-width="1.6" fill="none"/></svg>
        www.yourwebsitename.com
      </li>
    </ul>

    <div class="brand-seal">Corvane<br>Capital</div>
  </section>

  <section class="card card-back" aria-label="Business card back">
    <div class="back-pattern" role="img" aria-label="Repeating pattern of the brand mark in rows, glossy silver at the top left fading into the navy ground"></div>
    <div class="back-seal">Corvane<br>Capital</div>
  </section>

</main>
</body>
</html>
```